Water ATM Card

Need a design for water ATM cards. Size of card is 3.375 x 2.125 inch
On the Front include the Cedar hollow Logo.
Bottom right corner should have Price $100
On the Back
This card is to be used to access water refills at any Cedar Hollow Water Vending Machines.
Please contact (869) 418 2930 or (869) 534 1276 or email clearflowbox@mailvista.example for any assistance or recharging of card.

```html
<!DOCTYPE html>
<html lang="en">
<head>
<meta charset="utf-8">
<title>Cedar Hollow Water Card</title>
<link rel="stylesheet" href="https://fonts.googleapis.com/css2?family=Montserrat:wght@400;500;700;800&display=swap">
<style>
  :root {
    --stage: #9b9b9b;
    --card-white: #ffffff;
    --brand-blue: #2b5aa8;
    --brand-blue-light: #2a74c2;
    --ink: #1e1e24;
    --price-green: #32a046;
    --back-top: #2f80c0;
    --back-mid: #3a4f98;
    --back-bottom: #2a3a88;
    --back-brand: #2a3c80;
    --back-text: #e8ecf8;
  }
  * { box-sizing: border-box; margin: 0; padding: 0; }
  html, body {
    width: 1093px; height: 1200px; overflow: hidden;
    background: var(--stage);
    font-family: "Montserrat", sans-serif;
  }
  .card {
    position: absolute; left: 264px; width: 581px;
    border-radius: 18px; overflow: hidden;
  }
  .card--front { top: 225px; height: 363px; background: var(--card-white); }
  .card--back { top: 616px; height: 366px; }

  .brand-name {
    position: absolute; left: 0; width: 312px; top: 186px;
    text-align: center; font-weight: 700; font-size: 20px;
    color: var(--brand-blue-light); letter-spacing: 0.5px;
  }
  .divider {
    position: absolute; left: 281px; top: 126px;
    width: 1.5px; height: 145px; background: var(--brand-blue);
  }
  .holder { position: absolute; left: 292px; top: 125px; }
  .holder__name {
    font-weight: 800; font-size: 20px; color: var(--brand-blue); letter-spacing: 0.3px;
  }
  .holder__role { font-size: 13px; color: var(--ink); margin-top: 3px; }

  .contacts { position: absolute; left: 292px; top: 186px; list-style: none; }
  .contacts li {
    display: flex; align-items: center; gap: 6px;
    font-size: 13.5px; color: var(--ink); height: 22px;
  }
  .contacts li.gap-after { margin-bottom: 4px; }
  .contacts svg { width: 12px; height: 12px; fill: var(--brand-blue); flex: none; }

  .price {
    position: absolute; right: 38px; top: 311px;
    font-weight: 800; font-size: 18.5px; color: var(--price-green);
  }

  .back-pattern {
    position: absolute; inset: 0;
    background: linear-gradient(160deg, var(--back-top) 0%, var(--back-mid) 55%, var(--back-bottom) 100%);
  }
  .back-brand {
    position: absolute; left: 0; right: 0; top: 196px;
    text-align: center; font-weight: 700; font-size: 26px;
    color: var(--back-brand); letter-spacing: 0.5px;
  }
  .back-info {
    position: absolute; left: 30px; right: 30px; top: 248px;
    text-align: center; color: var(--back-text);
    font-size: 12px; line-height: 1.55;
  }
  .back-info .back-note { font-size: 13.5px; margin-top: 4px; }
</style>
</head>
<body>
  <section class="card card--front">
    <div class="brand-name">CEDAR HOLLOW</div>
    <div class="divider"></div>
    <div class="holder">
      <div class="holder__name">DANIEL REYES</div>
      <div class="holder__role">OWER</div>
    </div>
    <ul class="contacts">
      <li class="gap-after">
        <svg viewBox="0 0 24 24"><path d="M6.6 10.8a15 15 0 0 0 6.6 6.6l2.2-2.2a1 1 0 0 1 1-.25 11.4 11.4 0 0 0 3.6.57 1 1 0 0 1 1 1V20a1 1 0 0 1-1 1A17 17 0 0 1 3 4a1 1 0 0 1 1-1h3.5a1 1 0 0 1 1 1c0 1.25.2 2.450.57 3.57a1 1 0 0 1-.25 1z"/></svg>
        (869) 418 2930
      </li>
      <li class="gap-after">
        <svg viewBox="0 0 24 24"><path d="M7 1h10a2 2 0 0 1 2 2v18a2 2 0 0 1-2 2H7a2 2 0 0 1-2-2V3a2 2 0 0 1 2-2zm0 3v14h10V4zm5 15.5a1.2 1.2 0 1 0 0 2.4 1.2 1.2 0 0 0 0-2.4z"/></svg>
        (869) 534 1276
      </li>
      <li>
        <svg viewBox="0 0 24 24"><path d="M2 5h20v2l-10 6L2 7zm0 4 10 6 10-6v10H2z"/></svg>
        clearflowbox@mailvista.example
      </li>
      <li>
        <svg viewBox="0 0 24 24"><path d="M12 2a10 10 0 1 0 0 20 10 10 0 0 0 0-20zm0 2c.8 1.2 1.5 2.5 1.9 4h-3.8c.4-1.5 1.1-2.8 1.9-4zM4.3 14a8 8 0 0 1 0-4h3.4a16 16 0 0 0 0 4zm10 0H9.7a14.6 14.6 0 0 1 0-4h4.6a14.6 14.6 0 0 1 0 4zm2 0a16 16 0 0 0 0-4h3.4a8 8 0 0 1 0 4zM12 20c-.8-1.2-1.5-2.5-1.9-4h3.8c-.4 1.5-1.1 2.8-1.9 4z"/></svg>
        www.cedarhollowwater.example
      </li>
    </ul>
    <div class="price">Price $100</div>
  </section>

  <section class="card card--back">
    <div class="back-pattern" role="img" aria-label="Blue gradient field with a repeating pattern of brand symbols"></div>
    <div class="back-brand">CEDAR HOLLOW</div>
    <div class="back-info">
      <p>This card is to be used to access water refills at any Cedar Hollow Water Vending Machines.</p>
      <p>Please contact (869) 418 2930 or (869) 534 1276 or email clearflowbox@mailvista.example</p>
      <p class="back-note">for any assistance or recharging of card.</p>
    </div>
  </section>
</body>
</html>
```